Seeking for catalogue design -for Event Mgmt company

Need to be creative and striking and images to be more enhanced.
The items in the catalogue have to be layout well and easy to read.
Cover and background of catalogue needs to be striking but not overpowering the items.
Catologue needs to be able to put up on website and able to read on mobile.
Font used must be easily readable and not too small.

Target Market(s)

Business and Public Sectors

Industry/Entity Type

Event Planning

Colors

Designer to choose colors to be used in the design.

Requirements
Must have
• Not too many colors but must be creative
Nice to have
• See that the images of items in catalogue have better layout
Should not have
• Not to be so messy

```html
<!DOCTYPE html>
<html lang="en">
<head>
<meta charset="utf-8">
<title>Brightfield Events – Game Stalls</title>
<link href="https://fonts.googleapis.com/css2?family=Open+Sans:wght@400;700&display=swap" rel="stylesheet">
<style>
  :root{
    --ink:#2f3d45;
    --heading:#3b4b55;
    --mint:#b3e9e5;
    --mint-pale:#c9f0ec;
    --teal:#7ecdd4;
    --teal-deep:#73c3cb;
    --brand-box:#8f8683;
    --frame:#8a8a8a;
    --white:#ffffff;
  }
  *{margin:0;padding:0;box-sizing:border-box}
  html,body{width:848px;height:1200px;overflow:hidden;background:var(--white)}
  body{font-family:"Open Sans",Arial,sans-serif;color:var(--ink);position:relative}
  .backdrop{position:absolute;inset:0;width:848px;height:1200px}
  .brand{position:absolute;left:0;top:0;width:196px;height:63px;background:var(--brand-box);
    box-shadow:3px 3px 4px rgba(0,0,0,.25);color:var(--white);text-align:center;padding-top:8px}
  .brand-name{font-size:25px;font-weight:400;letter-spacing:1px;line-height:30px}
  .brand-sub{font-size:8px;letter-spacing:1px;line-height:12px}
  .page-no{position:absolute;right:8px;top:2px;color:var(--white);font-size:40px;font-weight:700}
  .item{position:absolute;text-align:center}
  .item-title{font-size:15.5px;font-weight:700;color:var(--heading);letter-spacing:.4px;white-space:nowrap;position:absolute;left:50%;transform:translateX(-50%)}
  .item-photo{position:absolute;border:4px solid var(--frame);border-bottom-width:14px;border-bottom-color:var(--white);
    outline:3px solid var(--frame);outline-offset:-1px;box-shadow:5px 6px 5px rgba(0,0,0,.3)}
  .item-info{position:absolute;left:50%;transform:translateX(-50%);white-space:nowrap;font-size:16.5px;line-height:20.5px}
  .item-info.small{font-size:15px;line-height:19px}
  .notes{position:absolute;left:0;top:1126px;width:848px;height:74px;border-top:1px solid #555;padding:8px 0 0 30px}
  .notes p{font-size:15px;font-weight:700;color:var(--heading);line-height:18.5px;letter-spacing:.3px;white-space:nowrap}
</style>
</head>
<body>
<svg class="backdrop" viewBox="0 0 848 1200" aria-hidden="true">
  <path d="M548,0 C540,190 640,320 848,332 L848,0 Z" fill="var(--mint)"/>
  <path d="M606,0 C600,150 700,300 848,325 L848,0 Z" fill="var(--teal)"/>
  <path d="M0,372 C120,325 330,300 470,345 C650,405 800,560 848,720 L848,1200 L0,1200 Z" fill="var(--mint)"/>
  <path d="M0,565 C150,495 380,470 540,505 C700,545 780,640 820,760 C600,640 700,900 848,1000 L848,1200 L0,1200 Z" fill="var(--teal)"/>
  <path d="M660,660 C740,720 848,800 848,900 L848,1000 C760,900 700,800 660,660 Z" fill="var(--mint-pale)"/>
  <rect x="0" y="1126" width="848" height="74" fill="var(--teal-deep)"/>
</svg>

<div class="brand"><div class="brand-name">BRIGHTFIELD</div><div class="brand-sub">BRIGHTFIELD EVENTS PTE LTD</div></div>
<div class="page-no">05</div>

<!-- Row 1 -->
<div class="item" style="left:0;top:0;width:848px;height:0">
  <div class="item-title" style="left:123px;top:72px">PREMIUM GAME STALL</div>
  <div class="item-photo" style="left:38px;top:104px;width:165px;height:172px;background:linear-gradient(160deg,#3c5a4a,#2c4a3e 60%,#8a6f55)" role="img" aria-label="Foosball table with red and blue players"></div>
  <div class="item-info" style="left:135px;top:298px">Foosball Table<br>Approx 1.2m by 0.5m<br>$420/stall<br>Subsequent day: $120</div>

  <div class="item-title" style="left:442px;top:72px">PREMIUM GAME STALL</div>
  <div class="item-photo" style="left:356px;top:106px;width:165px;height:172px;background:linear-gradient(180deg,#000 0%,#1b46c8 45%,#e2b13a 75%,#1e4fd8)" role="img" aria-label="Racked pool balls on a blue pool table"></div>
  <div class="item-info" style="left:442px;top:293px">Pool Table<br>6 foot pool table<br>$540/stall<br>Subsequent day: $140</div>

  <div class="item-title" style="left:731px;top:72px">PREMIUM GAME STALL</div>
  <div class="item-photo" style="left:659px;top:98px;width:139px;height:187px;background:linear-gradient(180deg,#b06a3e,#2d2d2d 25%,#333 75%,#c8642a)" role="img" aria-label="Digital basketball arcade game with basketballs"></div>
  <div class="item-info" style="left:727px;top:293px">Large Digital Basketball<br>1.1m by 1.9m by 2m<br>$420/stall<br>Subsequent day: $170</div>

  <!-- Row 2 -->
  <div class="item-title" style="left:128px;top:424px">PREMIUM GAME STALL</div>
  <div class="item-photo" style="left:49px;top:451px;width:139px;height:188px;background:linear-gradient(90deg,#f06a2a,#8c9399 50%,#42d04a)" role="img" aria-label="Two small spiral capsule machines, orange and green"></div>
  <div class="item-info" style="left:127px;top:655px">Small Capsule Machine<br>0.5m by 1.35m<br>$300/stall<br>Subsequent day: $120</div>

  <div class="item-title" style="left:425px;top:424px">PREMIUM GAME STALL</div>
  <div class="item-photo" style="left:355px;top:451px;width:139px;height:188px;background:linear-gradient(180deg,#f4f4f4 10%,#7a9a6a 30%,#d8262a 55%,#d8262a 85%,#fff)" role="img" aria-label="Three large red capsule machines"></div>
  <div class="item-info" style="left:428px;top:663px">Large Capsule Machine<br>0.35m by 1.47m (H)<br>$420/stall<br>Subsequent day: $120</div>

  <div class="item-title" style="left:734px;top:424px">PREMIUM GAME STALL</div>
  <div class="item-photo" style="left:638px;top:457px;width:165px;height:172px;background:linear-gradient(150deg,#5f7a45,#4f6a3a 50%,#c9283a 70%,#5a7444)" role="img" aria-label="Red pump blaster game units on grass"></div>
  <div class="item-info" style="left:720px;top:660px">Pump Blaster<br>Approx 0.5m/unit<br>$540 (2 units)<br>Subsequent day: $270</div>

  <!-- Row 3 -->
  <div class="item-title" style="left:133px;top:777px">TRADITIONAL GAME STALL</div>
  <div class="item-photo" style="left:38px;top:812px;width:165px;height:172px;background:linear-gradient(180deg,#e8453e,#3a2a2a 35%,#d8403c 60%,#1d1d1d)" role="img" aria-label="Congkak board and five stones on a red table"></div>
  <div class="item-info small" style="left:142px;top:1005px">Five Stones, Congkak, Tikam Tikam<br>oconut Bowling, Pickup Sticks, Marbl<br>Hopscotch, Bottle Ring Toss, Chapteh<br>$340/4 Traditional Games<br>Manpower $20/hour/pax</div>

  <div class="item-title" style="left:424px;top:779px">MOTION PLAY STATION</div>
  <div class="item-photo" style="left:340px;top:814px;width:165px;height:172px;background:linear-gradient(120deg,#b8a48c,#6f5a44 50%,#e6d6c8)" role="img" aria-label="Children playing a motion game in front of a screen"></div>
  <div class="item-info small" style="left:431px;top:1007px">Motion Play Station<br>Space required: 2m by 2m<br>$540/station<br>Require 1x Powerpoint (500W)<br>Subsequent day: $220</div>

  <div class="item-title" style="left:720px;top:779px">CONSOLE PLAY STATION</div>
  <div class="item-photo" style="left:638px;top:814px;width:165px;height:172px;background:linear-gradient(120deg,#2a3036,#3a8fa8 45%,#1c1c1c)" role="img" aria-label="Guests playing a console game on a screen"></div>
  <div class="item-info small" style="left:716px;top:1002px">Console Play Station<br>Space required: 2m by 2m<br>$700/station<br>Require 1x Powerpoint (500W)<br>Subsequent day: $220</div>
</div>

<div class="notes">
  <p>*Size stated above is estimated only.</p>
  <p>*Rates include Delivery, Set up, Dismantle and Collection of the equipments.</p>
  <p>*The more items or more days rented, we may be able to quote a much better discounted package rate</p>
</div>
</body>
</html>
```